Business Card for Field Bloom-Eco Friendly Organic Clothing Brand

We are looking for an amazing business card for our eco friendly, organic clothing brand. We are thinking maybe a business card with a peel off sticker on the back, since our hanging clothing tag is a peel off sticker on the back. I will attach our hang tag so we can make sure we stay in line with our design. I've also attached a bag we are doing because I do like the scattered emblem look as well.

```html
<!DOCTYPE html>
<html lang="en">
<head>
<meta charset="utf-8">
<title>Field Bloom Business Card</title>
<link href="https://fonts.googleapis.com/css2?family=Arimo:wght@400;700&display=swap" rel="stylesheet">
<style>
  :root {
    --page-bg: #e9e6e0;
    --card-black: #141414;
    --card-black-soft: #242424;
    --gold: #d9a520;
    --ink: #1b1b1b;
    --ink-soft: #555555;
    --paper: #ffffff;
    --divider: #cfcfcf;
    --url-grey: #e6e6e6;
  }
  * { margin: 0; padding: 0; box-sizing: border-box; }
  html, body { width: 1200px; height: 950px; overflow: hidden; }
  body {
    background: var(--page-bg);
    font-family: "Arimo", Arial, sans-serif;
    position: relative;
  }
  .card {
    position: absolute;
    left: 250px;
    width: 700px;
    height: 400px;
    border-radius: 22px;
    overflow: hidden;
  }

  /* Back side */
  .card-back { top: 40px; background: var(--card-black); }
  .back-pattern {
    position: absolute; inset: 0;
    background: radial-gradient(ellipse at 40% 40%, var(--card-black-soft), var(--card-black) 70%);
  }
  .brand-panel {
    position: absolute;
    left: 180px; top: 95px;
    width: 340px; height: 150px;
    border-radius: 14px;
    border: 4px solid var(--gold);
    background: var(--card-black);
    display: flex; align-items: center; justify-content: center; gap: 16px;
  }
  .brand-panel-mark {
    width: 30px; height: 30px;
    border-radius: 50%;
    background: var(--gold);
  }
  .brand-panel-name {
    font-size: 36px; font-weight: 700;
    color: var(--gold);
  }
  .back-url {
    position: absolute;
    left: 0; right: 0; top: 275px;
    text-align: center;
    color: var(--url-grey);
    font-size: 17px;
    letter-spacing: 3px;
  }

  /* Front side */
  .card-front {
    top: 500px;
    background: var(--card-black);
    padding: 14px;
  }
  .front-face {
    width: 100%; height: 100%;
    border-radius: 14px;
    background: var(--paper);
    border: 3px solid var(--gold);
    position: relative;
  }
  .brand {
    position: absolute;
    left: 50px; top: 140px;
    display: flex; align-items: center; gap: 14px;
  }
  .brand-mark {
    width: 34px; height: 34px;
    background: var(--ink);
  }
  .brand-name {
    font-size: 34px; font-weight: 700;
    color: var(--ink);
  }
  .divider {
    position: absolute;
    left: 330px; top: 70px;
    width: 1px; height: 230px;
    background: var(--divider);
  }
  .contact {
    position: absolute;
    left: 365px; top: 70px;
    color: var(--ink-soft);
  }
  .person-name { font-size: 26px; font-weight: 700; color: var(--ink); }
  .person-title { font-size: 17px; color: var(--ink); margin-bottom: 16px; margin-top: 2px; }
  .contact-line {
    display: flex; align-items: center; gap: 10px;
    font-size: 19px; line-height: 28px;
  }
  .contact-line svg { width: 18px; height: 18px; flex: none; }
  .contact-line .spacer { width: 18px; flex: none; }
</style>
</head>
<body>

<section class="card card-back">
  <div class="back-pattern" role="img" aria-label="Faint scattered decorative word pattern"></div>
  <div class="brand-panel">
    <span class="brand-panel-mark"></span>
    <span class="brand-panel-name">Field Bloom</span>
  </div>
  <p class="back-url">www.fieldbloom.com</p>
</section>

<section class="card card-front">
  <div class="front-face">
    <div class="brand">
      <span class="brand-mark"></span>
      <span class="brand-name">Field Bloom</span>
    </div>
    <div class="divider"></div>
    <div class="contact">
      <p class="person-name">Sam Rowe</p>
      <p class="person-title">President</p>
      <p class="contact-line"><span class="spacer"></span>4120 Cedar Hollow Lane</p>
      <p class="contact-line"><span class="spacer"></span>Maple Grove, NY 12040</p>
      <p class="contact-line">
        <svg viewBox="0 0 18 18"><path d="M4 2 L7 2 L8 6 L6 7.5 A10 10 0 0 0 10.5 12 L12 10 L16 11 L16 14 A2 2 0 0 1 14 16 A13 13 0 0 1 2 4 A2 2 0 0 1 4 2Z" fill="var(--gold)"/></svg>
        555 0142 7781
      </p>
      <p class="contact-line">
        <svg viewBox="0 0 18 18"><rect x="5" y="1" width="8" height="16" rx="1.5" fill="var(--gold)"/><rect x="6.5" y="3" width="5" height="10" fill="var(--paper)"/></svg>
        555 0198 3364
      </p>
      <p class="contact-line">
        <svg viewBox="0 0 18 18"><rect x="5" y="2" width="8" height="5" fill="var(--gold)"/><rect x="2" y="7" width="14" height="8" rx="1.5" fill="var(--gold)"/></svg>
        555 0176 2290
      </p>
      <p class="contact-line">
        <svg viewBox="0 0 18 18"><rect x="1" y="4" width="16" height="11" rx="1" fill="var(--gold)"/><path d="M1 4 L9 10 L17 4" stroke="var(--paper)" stroke-width="1.5" fill="none"/></svg>
        info@fieldbloom.com
      </p>
    </div>
  </div>
</section>

</body>
</html>
```